Business Cards for a law firm

Business cards for our law firm. Use our silhoette logo and OAK PARTNERS - check our website (www.oakpartners.example)

Contact Information for Business Card

our silhouette logo, OAK PARTNERS, 800-555-0147, Dorian Pemberton, dorian@oakpartners.example

Requirements
Must have
• our silhouette logo, OAK PARTNERS, 800-555-0147, Dorian Pemberton, dorian@oakpartners.example

```html
<!DOCTYPE html>
<html lang="en">
<head>
<meta charset="utf-8">
<title>Oak Partners – Business Card</title>
<link rel="stylesheet" href="https://fonts.googleapis.com/css2?family=Montserrat:wght@300;400;700&display=swap">
<style>
  :root {
    --navy: #22346f;
    --paper: #ffffff;
    --ink: #1f1f24;
    --rule: #5a5f8c;
    --backdrop: #2b2b2d;
  }
  * { box-sizing: border-box; margin: 0; padding: 0; }
  html, body { width: 1200px; height: 900px; overflow: hidden; }
  body {
    background: var(--backdrop);
    font-family: "Montserrat", sans-serif;
    position: relative;
  }
  .card {
    position: absolute;
    top: 100px;
    width: 400px;
    height: 700px;
    box-shadow: 0 12px 30px rgba(0,0,0,.45);
  }
  .card--front { left: 160px; background: var(--paper); color: var(--navy); }
  .card--back  { left: 640px; background: var(--navy); display: flex; align-items: center; justify-content: center; }

  .firm-name {
    position: absolute; top: 58px; left: 0; right: 0;
    text-align: center; font-weight: 700; font-size: 34px; letter-spacing: 2px;
  }
  .brand-mark {
    position: absolute; top: 138px; left: 50%;
    width: 150px; height: 200px; margin-left: -75px;
    background: var(--navy);
  }
  .person-name {
    position: absolute; top: 378px; left: 0; right: 0;
    text-align: center; font-weight: 700; font-size: 27px; letter-spacing: 1px;
  }
  .person-role {
    position: absolute; top: 414px; left: 0; right: 0;
    text-align: center; font-weight: 400; font-size: 17px; color: var(--ink); letter-spacing: 1px;
  }
  .divider {
    position: absolute; left: 40px; right: 40px; height: 26px;
    display: flex; align-items: center; gap: 12px;
  }
  .divider::before, .divider::after {
    content: ""; flex: 1; height: 1px; background: var(--rule);
  }
  .divider--contact { top: 452px; }
  .divider--address { top: 584px; }
  .icon { width: 24px; height: 24px; display: block; }
  .icon-group { display: flex; gap: 5px; }
  .contact-list {
    position: absolute; top: 490px; left: 0; right: 0;
    text-align: center; color: var(--ink); font-size: 16px; line-height: 28px; font-weight: 400;
    list-style: none;
  }
  .address {
    position: absolute; top: 620px; left: 0; right: 0;
    text-align: center; color: var(--ink); font-size: 16px; line-height: 26px; font-style: normal;
  }
  .back-name {
    color: var(--paper); font-weight: 700; font-size: 40px; letter-spacing: 3px; text-align: center;
  }
</style>
</head>
<body>
  <section class="card card--front">
    <h1 class="firm-name">OAK PARTNERS</h1>
    <div class="brand-mark" role="img" aria-label="Firm silhouette logo"></div>
    <h2 class="person-name">DORIAN PEMBERTON</h2>
    <p class="person-role">OWNER</p>

    <div class="divider divider--contact">
      <div class="icon-group">
        <svg class="icon" viewBox="0 0 24 24" aria-hidden="true"><rect width="24" height="24" rx="5" fill="#22346f"/><path d="M6 14c0-4 3-6 6-6s6 2 6 6v3H6z" fill="#fff"/><rect x="9" y="12" width="6" height="3" fill="#22346f"/></svg>
        <svg class="icon" viewBox="0 0 24 24" aria-hidden="true"><rect width="24" height="24" rx="5" fill="#22346f"/><rect x="5" y="7" width="14" height="10" fill="#fff"/><path d="M5 7l7 6 7-6" stroke="#22346f" stroke-width="1.6" fill="none"/></svg>
        <svg class="icon" viewBox="0 0 24 24" aria-hidden="true"><rect width="24" height="24" rx="5" fill="#22346f"/><circle cx="12" cy="12" r="6.5" fill="#fff"/><path d="M5.5 12h13M12 5.5v13" stroke="#22346f" stroke-width="1.3"/></svg>
      </div>
    </div>

    <ul class="contact-list">
      <li>800-555-0147</li>
      <li>dorian@oakpartners.example</li>
      <li>www.oakpartners.example</li>
    </ul>

    <div class="divider divider--address">
      <svg class="icon" viewBox="0 0 24 24" aria-hidden="true"><rect width="24" height="24" rx="5" fill="#22346f"/><path d="M12 19s-5-5-5-9a5 5 0 0 1 10 0c0 4-5 9-5 9z" fill="#fff"/><circle cx="12" cy="10" r="2" fill="#22346f"/></svg>
    </div>

    <address class="address">4120 Meridian Ave #305,<br>Oakdale Hills, CA 90000</address>
  </section>

  <section class="card card--back">
    <p class="back-name">OAK PARTNERS</p>
  </section>
</body>
</html>
```